MRT Property - Business Cards

Looking for a business card & general letterhead, signage etc design for our new logo.

Colours:
000a20
0056a2
00b5ef
0088ce
68cef2

Fonts:
Poppins
Karla

Please keep look and feel of new brand - example in the zip package I sent.

```html
<!DOCTYPE html>
<html lang="en">
<head>
<meta charset="utf-8">
<title>MRT Property – Stationery</title>
<link rel="stylesheet" href="https://fonts.googleapis.com/css2?family=Poppins:wght@400;500;600&display=swap">
<style>
  :root{
    --ink:#000a20;
    --navy:#0056a2;
    --blue:#0088ce;
    --cyan:#00b5ef;
    --sky:#68cef2;
    --paper:#ffffff;
    --paper-soft:#f2f3f4;
    --backdrop:#8c8c8c;
    --wire:#1e2226;
  }
  *{box-sizing:border-box;margin:0;padding:0}
  html,body{width:1200px;height:686px;overflow:hidden}
  body{background:var(--backdrop);font-family:"Poppins",sans-serif;color:var(--ink);position:relative}

  .sheet{position:absolute;background:var(--paper);box-shadow:0 6px 18px rgba(0,0,0,.28);overflow:hidden}

  /* shared brand parts */
  .brand{position:absolute;display:flex;align-items:center;gap:6px;color:var(--blue);font-weight:600;white-space:nowrap}
  .brand-dot{border-radius:50%;background:var(--blue);flex:none}
  .header-rule{position:absolute;left:0;right:0;height:1px;background:var(--sky)}
  .header-rule-accent{position:absolute;height:3px;background:var(--navy)}
  .footer-rule{position:absolute;left:0;right:0;height:1px;background:var(--sky)}
  .footer-rule-accent{position:absolute;height:2px;background:var(--navy)}
  .contact{position:absolute;display:flex;flex-direction:column;font-weight:400;color:var(--ink);white-space:nowrap}
  .contact-item{display:flex;align-items:center;gap:4px;line-height:1.2}
  .contact-item svg{flex:none;fill:var(--blue)}
  .edge-bands{position:absolute;left:0;bottom:0;width:100%}

  /* letterhead */
  .letterhead{left:60px;top:100px;width:350px;height:495px}
  .letterhead .brand{right:28px;top:40px;font-size:19px}
  .letterhead .brand-dot{width:12px;height:12px}
  .letterhead .header-rule{top:82px}
  .letterhead .header-rule-accent{top:81px;left:190px;width:135px}
  .letterhead .footer-rule{top:418px}
  .letterhead .footer-rule-accent{top:417px;left:80px;width:170px}
  .letterhead .contact{left:18px;top:425px;gap:3px;font-size:7.6px}
  .letterhead .edge-bands{height:18px}

  /* notepad */
  .notepad{left:450px;top:78px;width:330px;height:238px;box-shadow:0 8px 0 -2px #2a2e33,0 10px 20px rgba(0,0,0,.35)}
  .notepad-wire{position:absolute;left:450px;top:62px;width:330px;height:26px;display:flex;justify-content:space-between;padding:0 10px;z-index:2}
  .notepad-wire span{width:8px;height:24px;border:2.5px solid var(--wire);border-radius:5px;background:transparent}
  .notepad .brand{right:22px;top:44px;font-size:17px}
  .notepad .brand-dot{width:10px;height:10px}
  .notepad .header-rule{top:78px}
  .notepad .header-rule-accent{top:77px;left:170px;width:140px}
  .notepad .footer-rule{top:172px}
  .notepad .footer-rule-accent{top:171px;left:70px;width:150px}
  .notepad .contact{left:14px;top:178px;gap:2px;font-size:6.4px}
  .notepad .edge-bands{height:14px}

  /* business card */
  .card{left:815px;top:92px;width:320px;height:184px;background:var(--paper-soft)}
  .card .brand{right:20px;top:36px;font-size:17px}
  .card .brand-dot{width:10px;height:10px}
  .card .header-rule{top:70px}
  .card .header-rule-accent{top:69px;left:170px;width:130px}
  .card .footer-rule{top:114px}
  .card .footer-rule-accent{top:113px;left:60px;width:140px}
  .card .contact{left:14px;top:120px;gap:2px;font-size:6.8px}
  .card .edge-bands{height:13px}

  /* envelope */
  .envelope{position:absolute;left:600px;top:380px;width:460px;height:230px;background:var(--navy);box-shadow:0 6px 18px rgba(0,0,0,.3);overflow:hidden}
  .envelope-flap{position:absolute;left:0;top:0;width:100%;height:100%}
  .envelope-seal{position:absolute;left:50%;top:96px;width:18px;height:18px;margin-left:-9px;border-radius:50%;background:var(--sky)}
</style>
</head>
<body>

<!-- Letterhead -->
<section class="sheet letterhead" aria-label="Letterhead">
  <div class="brand"><span class="brand-dot"></span>MRT Property</div>
  <div class="header-rule"></div>
  <div class="header-rule-accent"></div>
  <div class="footer-rule"></div>
  <div class="footer-rule-accent"></div>
  <div class="contact">
    <div class="contact-item"><svg width="8" height="8" viewBox="0 0 10 10"><path d="M2 0.5l2 2-1 1.3c.6 1.3 1.5 2.2 2.8 2.8L7.1 5.6l2 2-1.3 1.8C4.5 9.2.8 5.5.5 2.2z"/></svg>+61 2 9000 4812</div>
    <div class="contact-item"><svg width="8" height="8" viewBox="0 0 10 10"><path d="M5 0a3.4 3.4 0 0 0-3.4 3.4C1.6 6 5 10 5 10s3.4-4 3.4-6.6A3.4 3.4 0 0 0 5 0zm0 4.8a1.4 1.4 0 1 1 0-2.8 1.4 1.4 0 0 1 0 2.8z"/></svg>Suite 3.14, Level 1, 18 Harbourline Way, Rivergate NSW 2199</div>
    <div class="contact-item"><svg width="8" height="8" viewBox="0 0 10 10"><path d="M0 2h10v6H0z"/></svg>hello@mrtproperty.example</div>
    <div class="contact-item"><svg width="8" height="8" viewBox="0 0 10 10"><circle cx="5" cy="5" r="5"/></svg>www.mrtproperty.example</div>
  </div>
  <svg class="edge-bands" viewBox="0 0 350 18" preserveAspectRatio="none">
    <polygon points="0,0 150,0 168,18 0,18" fill="var(--blue)"/>
    <polygon points="150,9 280,9 280,18 159,18" fill="var(--sky)"/>
  </svg>
</section>

<!-- Notepad -->
<div class="notepad-wire" aria-hidden="true">
  <span></span><span></span><span></span><span></span><span></span><span></span><span></span><span></span><span></span><span></span><span></span><span></span><span></span><span></span><span></span><span></span><span></span><span></span><span></span><span></span>
</div>
<section class="sheet notepad" aria-label="Notepad">
  <div class="brand"><span class="brand-dot"></span>MRT Property</div>
  <div class="header-rule"></div>
  <div class="header-rule-accent"></div>
  <div class="footer-rule"></div>
  <div class="footer-rule-accent"></div>
  <div class="contact">
    <div class="contact-item"><svg width="7" height="7" viewBox="0 0 10 10"><path d="M2 0.5l2 2-1 1.3c.6 1.3 1.5 2.2 2.8 2.8L7.1 5.6l2 2-1.3 1.8C4.5 9.2.8 5.5.5 2.2z"/></svg>+61 2 9000 4812</div>
    <div class="contact-item"><svg width="7" height="7" viewBox="0 0 10 10"><path d="M5 0a3.4 3.4 0 0 0-3.4 3.4C1.6 6 5 10 5 10s3.4-4 3.4-6.6A3.4 3.4 0 0 0 5 0zm0 4.8a1.4 1.4 0 1 1 0-2.8 1.4 1.4 0 0 1 0 2.8z"/></svg>Suite 3.14, Level 1, 18 Harbourline Way, Rivergate NSW 2199</div>
    <div class="contact-item"><svg width="7" height="7" viewBox="0 0 10 10"><path d="M0 2h10v6H0z"/></svg>hello@mrtproperty.example</div>
    <div class="contact-item"><svg width="7" height="7" viewBox="0 0 10 10"><circle cx="5" cy="5" r="5"/></svg>www.mrtproperty.example</div>
  </div>
  <svg class="edge-bands" viewBox="0 0 330 14" preserveAspectRatio="none">
    <polygon points="0,0 140,0 154,14 0,14" fill="var(--blue)"/>
    <polygon points="140,7 270,7 270,14 147,14" fill="var(--sky)"/>
  </svg>
</section>

<!-- Business card -->
<section class="sheet card" aria-label="Business card">
  <div class="brand"><span class="brand-dot"></span>MRT Property</div>
  <div class="header-rule"></div>
  <div class="header-rule-accent"></div>
  <div class="footer-rule"></div>
  <div class="footer-rule-accent"></div>
  <div class="contact">
    <div class="contact-item"><svg width="7" height="7" viewBox="0 0 10 10"><path d="M2 0.5l2 2-1 1.3c.6 1.3 1.5 2.2 2.8 2.8L7.1 5.6l2 2-1.3 1.8C4.5 9.2.8 5.5.5 2.2z"/></svg>+61 2 9000 4812</div>
    <div class="contact-item"><svg width="7" height="7" viewBox="0 0 10 10"><path d="M5 0a3.4 3.4 0 0 0-3.4 3.4C1.6 6 5 10 5 10s3.4-4 3.4-6.6A3.4 3.4 0 0 0 5 0zm0 4.8a1.4 1.4 0 1 1 0-2.8 1.4 1.4 0 0 1 0 2.8z"/></svg>Suite 3.14, Level 1, 18 Harbourline Way, Rivergate NSW 2199</div>
    <div class="contact-item"><svg width="7" height="7" viewBox="0 0 10 10"><path d="M0 2h10v6H0z"/></svg>hello@mrtproperty.example</div>
    <div class="contact-item"><svg width="7" height="7" viewBox="0 0 10 10"><circle cx="5" cy="5" r="5"/></svg>www.mrtproperty.example</div>
  </div>
  <svg class="edge-bands" viewBox="0 0 320 13" preserveAspectRatio="none">
    <polygon points="0,0 130,0 143,13 0,13" fill="var(--blue)"/>
    <polygon points="130,6 250,6 250,13 137,13" fill="var(--sky)"/>
  </svg>
</section>

<!-- Envelope -->
<section class="envelope" aria-label="Envelope">
  <svg class="envelope-flap" viewBox="0 0 460 230" preserveAspectRatio="none" aria-hidden="true">
    <polygon points="0,0 460,0 460,40 250,150 210,150 0,40" fill="#0a4f96"/>
    <polyline points="0,40 210,150 250,150 460,40" fill="none" stroke="#0a4586" stroke-width="2"/>
  </svg>
  <div class="envelope-seal"></div>
</section>

</body>
</html>
```